Rental Product Flyer

We have an outdated flyer that we give to prospective customers. The flyer describes the products we rent and has pictures or drawings. Would like to update with better pictures or maybe use drawings if that is better. Need to use the new logo (attached) and only list the following stores and phone numbers: Northeast - Greensburg, PA 800.555.0143; Mid-Atlantic Portsmouth, VA 888.555.0187; Gulf Coast - Houston Ship Channel - 281.555.0162; Louisiana - 225.555.0139

```html
<!DOCTYPE html>
<html lang="en">
<head>
<meta charset="utf-8">
<title>Iron Bay Rentals &amp; Supply — Rental Product Flyer</title>
<link rel="stylesheet" href="https://fonts.googleapis.com/css2?family=Lexend:wght@400;500;600&display=swap">
<style>
  :root {
    --board: #d6d4d6;
    --navy-deep: #121935;
    --navy-mid: #17244a;
    --navy-glow: #1f3f78;
    --brand-blue: #2f66c4;
    --text-light: #ffffff;
    --tile-frame: #ffffff;
    --shadow: rgba(0, 0, 0, 0.35);
  }
  * { box-sizing: border-box; margin: 0; padding: 0; }
  html, body { width: 1200px; height: 600px; overflow: hidden; }
  body {
    background: var(--board);
    font-family: "Lexend", sans-serif;
    color: var(--text-light);
    position: relative;
  }
  .page {
    position: absolute;
    top: 20px;
    width: 396px;
    height: 560px;
    background:
      linear-gradient(200deg, var(--navy-deep) 0%, var(--navy-deep) 45%, var(--navy-mid) 72%, var(--navy-glow) 100%);
    box-shadow: 6px 6px 10px var(--shadow);
    text-transform: uppercase;
  }
  .page--products { left: 184px; }
  .page--stores { left: 620px; }

  .brand {
    position: absolute;
    left: 0; right: 0;
    text-align: center;
  }
  .brand__name {
    font-weight: 600;
    color: var(--brand-blue);
    line-height: 1.05;
    letter-spacing: 0.5px;
  }
  .brand__tag {
    font-weight: 400;
    color: var(--brand-blue);
    letter-spacing: 0.4px;
  }
  .page--products .brand { top: 38px; }
  .page--products .brand__name { font-size: 26px; }
  .page--products .brand__tag { font-size: 7px; margin-top: 6px; }
  .page--stores .brand { top: 34px; }
  .page--stores .brand__name { font-size: 19px; }
  .page--stores .brand__tag { font-size: 5.5px; margin-top: 4px; }

  .headline {
    position: absolute;
    left: 0; right: 0;
    text-align: center;
    font-weight: 500;
    font-size: 15px;
  }
  .page--products .headline { top: 134px; }
  .page--stores .headline { top: 118px; font-size: 14px; }
  .subhead {
    position: absolute;
    top: 172px; left: 0; right: 0;
    text-align: center;
    font-weight: 500;
    font-size: 10px;
    line-height: 1.2;
  }

  .product {
    position: absolute;
    width: 98px;
    text-align: center;
  }
  .product__label {
    font-size: 8.6px;
    font-weight: 500;
    white-space: nowrap;
    height: 12px;
    line-height: 12px;
  }
  .product__label--small { font-size: 7.4px; }
  .product__photo {
    display: block;
    width: 98px;
    height: 65px;
    border: 2px solid var(--tile-frame);
  }

  .store {
    position: absolute;
    width: 134px;
    text-align: center;
  }
  .store__photo {
    display: block;
    width: 134px;
    height: 90px;
    border: 3px solid var(--tile-frame);
  }
  .store__line {
    display: flex;
    align-items: flex-start;
    justify-content: center;
    gap: 4px;
    font-size: 6.6px;
    font-weight: 500;
    line-height: 1.15;
    margin-top: 6px;
  }
  .store__line svg { flex: none; }

  .hq {
    position: absolute;
    top: 456px; left: 0; right: 0;
    text-align: center;
  }
  .hq__title { font-size: 11px; font-weight: 500; letter-spacing: 0.3px; }
  .hq__details { font-size: 8px; font-weight: 500; line-height: 1.25; margin-top: 8px; }
  .web {
    position: absolute;
    top: 522px; left: 0; right: 0;
    display: flex;
    justify-content: center;
    align-items: center;
    gap: 8px;
    font-size: 8.2px;
    font-weight: 500;
    line-height: 1.2;
  }
</style>
</head>
<body>

<section class="page page--products">
  <div class="brand">
    <div class="brand__name">Iron Bay<br>Rentals &amp; Supply</div>
    <div class="brand__tag">Abrasive Blasting &amp; Coating Equipment</div>
  </div>
  <h1 class="headline">Rent with confidence!</h1>
  <p class="subhead">Explore our wide range of quality<br>products for rent!</p>

  <div class="product" style="left:42px; top:224px;">
    <div class="product__label">Dust Collectors</div>
    <div class="product__photo" role="img" aria-label="Photo of a trailer-mounted dust collector" style="background:linear-gradient(160deg,#f4f4f4,#9a9ea4 55%,#f0f0f0)"></div>
  </div>
  <div class="product" style="left:149px; top:224px;">
    <div class="product__label">Decon Systems</div>
    <div class="product__photo" role="img" aria-label="Photo of a blue decontamination trailer" style="background:linear-gradient(160deg,#f4f4f4,#2f6fc0 40%,#1d4f9c 70%,#f0f0f0)"></div>
  </div>
  <div class="product" style="left:256px; top:224px;">
    <div class="product__label">Hand Tools</div>
    <div class="product__photo" role="img" aria-label="Photo of a pneumatic hand tool" style="background:linear-gradient(160deg,#f4f4f4,#3a3d44 55%,#f0f0f0)"></div>
  </div>

  <div class="product" style="left:42px; top:331px;">
    <div class="product__label product__label--small">Respiratory Systems</div>
    <div class="product__photo" role="img" aria-label="Photo of a green breathing air pump" style="background:linear-gradient(160deg,#f4f4f4,#3f9a5c 50%,#f0f0f0)"></div>
  </div>
  <div class="product" style="left:149px; top:331px;">
    <div class="product__label">Air Management</div>
    <div class="product__photo" role="img" aria-label="Photo of an air heater on a red skid" style="background:linear-gradient(170deg,#f4f4f4,#8c9096 45%,#c8323a 70%,#f0f0f0)"></div>
  </div>
  <div class="product" style="left:256px; top:331px;">
    <div class="product__label">Blasting Systems</div>
    <div class="product__photo" role="img" aria-label="Photo of a blue blast pot trailer" style="background:linear-gradient(160deg,#f4f4f4,#3b8fd6 50%,#f0f0f0)"></div>
  </div>

  <div class="product" style="left:42px; top:439px;">
    <div class="product__label product__label--small">Air Drying Systems</div>
    <div class="product__photo" role="img" aria-label="Photo of a blue air dryer unit" style="background:linear-gradient(160deg,#f4f4f4,#2f86cc 55%,#f0f0f0)"></div>
  </div>
  <div class="product" style="left:149px; top:439px;">
    <div class="product__label product__label--small">Air &amp; Power Systems</div>
    <div class="product__photo" role="img" aria-label="Photo of a towable air compressor" style="background:linear-gradient(160deg,#f4f4f4,#4d8a5a 40%,#2b2d31 65%,#f0f0f0)"></div>
  </div>
  <div class="product" style="left:256px; top:439px;">
    <div class="product__label product__label--small">High Volume Vacuums</div>
    <div class="product__photo" role="img" aria-label="Photo of a blue industrial vacuum unit" style="background:linear-gradient(160deg,#f4f4f4,#2f7fd0 50%,#f0f0f0)"></div>
  </div>
</section>

<section class="page page--stores">
  <div class="brand">
    <div class="brand__name">Iron Bay<br>Rentals &amp; Supply</div>
    <div class="brand__tag">Abrasive Blasting &amp; Coating Equipment</div>
  </div>
  <h2 class="headline">Our stores and phone numbers</h2>

  <div class="store" style="left:54px; top:159px;">
    <div class="store__photo" role="img" aria-label="Aerial view of Greensburg, Pennsylvania" style="background:linear-gradient(180deg,#b9c4cc 0%,#8d8a86 35%,#6f6a62 70%,#4f6a44 100%)"></div>
    <div class="store__line">
      <svg width="7" height="9" viewBox="0 0 10 13"><path d="M5 12 C2 8 1 6 1 4.5 A4 4 0 0 1 9 4.5 C9 6 8 8 5 12Z" fill="none" stroke="#fff" stroke-width="1"/><circle cx="5" cy="4.6" r="1.4" fill="none" stroke="#fff" stroke-width="1"/></svg>
      <span>Northeast - Greensburg, PA</span>
    </div>
    <div class="store__line">
      <svg width="8" height="8" viewBox="0 0 12 12"><path d="M2.5 1 L4.5 1 L5.5 3.8 L4.2 5 C5 6.8 5.8 7.6 7 8.2 L8.2 7 L11 8 L11 10 C11 10.6 10.5 11 10 11 C5 10.8 1.2 7 1 2 C1 1.5 1.5 1 2.5 1Z" fill="none" stroke="#fff" stroke-width="0.9"/></svg>
      <span>800.555.0143</span>
    </div>
  </div>

  <div class="store" style="left:210px; top:159px;">
    <div class="store__photo" role="img" aria-label="Aerial view of the Portsmouth, Virginia waterfront" style="background:linear-gradient(180deg,#c9d2da 0%,#7f8c8f 30%,#3c5364 60%,#6f7a74 100%)"></div>
    <div class="store__line">
      <svg width="7" height="9" viewBox="0 0 10 13"><path d="M5 12 C2 8 1 6 1 4.5 A4 4 0 0 1 9 4.5 C9 6 8 8 5 12Z" fill="none" stroke="#fff" stroke-width="1"/><circle cx="5" cy="4.6" r="1.4" fill="none" stroke="#fff" stroke-width="1"/></svg>
      <span>Mid-Atlantic - Portsmouth, VA</span>
    </div>
    <div class="store__line">
      <svg width="8" height="8" viewBox="0 0 12 12"><path d="M2.5 1 L4.5 1 L5.5 3.8 L4.2 5 C5 6.8 5.8 7.6 7 8.2 L8.2 7 L11 8 L11 10 C11 10.6 10.5 11 10 11 C5 10.8 1.2 7 1 2 C1 1.5 1.5 1 2.5 1Z" fill="none" stroke="#fff" stroke-width="0.9"/></svg>
      <span>888.555.0187</span>
    </div>
  </div>

  <div class="store" style="left:54px; top:300px;">
    <div class="store__photo" role="img" aria-label="Aerial view of a Louisiana riverfront and bridge" style="background:linear-gradient(180deg,#b7c3cf 0%,#8795a3 30%,#4f6a88 55%,#6a7670 100%)"></div>
    <div class="store__line">
      <svg width="7" height="9" viewBox="0 0 10 13"><path d="M5 12 C2 8 1 6 1 4.5 A4 4 0 0 1 9 4.5 C9 6 8 8 5 12Z" fill="none" stroke="#fff" stroke-width="1"/><circle cx="5" cy="4.6" r="1.4" fill="none" stroke="#fff" stroke-width="1"/></svg>
      <span>Louisiana</span>
    </div>
    <div class="store__line">
      <svg width="8" height="8" viewBox="0 0 12 12"><path d="M2.5 1 L4.5 1 L5.5 3.8 L4.2 5 C5 6.8 5.8 7.6 7 8.2 L8.2 7 L11 8 L11 10 C11 10.6 10.5 11 10 11 C5 10.8 1.2 7 1 2 C1 1.5 1.5 1 2.5 1Z" fill="none" stroke="#fff" stroke-width="0.9"/></svg>
      <span>225.555.0139</span>
    </div>
  </div>

  <div class="store" style="left:210px; top:300px;">
    <div class="store__photo" role="img" aria-label="Aerial view of the Houston Ship Channel industrial area" style="background:linear-gradient(180deg,#aeb4b6 0%,#8e9290 35%,#6d7472 60%,#4e6878 100%)"></div>
    <div class="store__line">
      <svg width="7" height="9" viewBox="0 0 10 13"><path d="M5 12 C2 8 1 6 1 4.5 A4 4 0 0 1 9 4.5 C9 6 8 8 5 12Z" fill="none" stroke="#fff" stroke-width="1"/><circle cx="5" cy="4.6" r="1.4" fill="none" stroke="#fff" stroke-width="1"/></svg>
      <span>Gulf Coast - Houston Ship<br>Channel</span>
    </div>
    <div class="store__line" style="margin-top:3px;">
      <svg width="8" height="8" viewBox="0 0 12 12"><path d="M2.5 1 L4.5 1 L5.5 3.8 L4.2 5 C5 6.8 5.8 7.6 7 8.2 L8.2 7 L11 8 L11 10 C11 10.6 10.5 11 10 11 C5 10.8 1.2 7 1 2 C1 1.5 1.5 1 2.5 1Z" fill="none" stroke="#fff" stroke-width="0.9"/></svg>
      <span>281.555.0162</span>
    </div>
  </div>

  <div class="hq">
    <div class="hq__title">Corporate Headquarters:</div>
    <div class="hq__details">480 Foundry Avenue • Greensburg, PA 15601<br>Office: 800-555-0143 • Fax: 800-555-0198</div>
  </div>

  <div class="web">
    <svg width="20" height="20" viewBox="0 0 20 20" fill="none" stroke="#fff" stroke-width="0.9">
      <circle cx="10" cy="10" r="8.5"/>
      <ellipse cx="10" cy="10" rx="3.8" ry="8.5"/>
      <line x1="1.5" y1="10" x2="18.5" y2="10"/>
      <path d="M3 5.5 H17 M3 14.5 H17"/>
    </svg>
    <div>www.ironbayrentals.com<br>sales@ironbayrentals.com</div>
  </div>
</section>

</body>
</html>
```